Need Business Card ASAP

We need a business card design for a meeting coming up in a few days. The company name is Harlow Ridge Building and Construction and the logo is attached. Something clean, cool, and contemporary that we can get to a printer right away. Attached is the business card for Volmar Energy, an affiliated company, which we like. Instead of the hawk on the back, you could use the attached "D". We'll also be needing matching letterhead in the near future, so ideas for that are welcome.

```html
<!DOCTYPE html>
<html lang="en">
<head>
<meta charset="utf-8">
<title>Harlow Ridge Building &amp; Construction — Business Card</title>
<link href="https://fonts.googleapis.com/css2?family=Source+Sans+3:wght@400;600;700&display=swap" rel="stylesheet">
<style>
  :root {
    --backdrop: #e6e1d6;
    --card-white: #ffffff;
    --olive: #c6bf85;
    --olive-light: #e4e0c2;
    --ink: #2b2a28;
    --ink-soft: #4a4946;
    --icon-grey: #9a9890;
    --divider: #b9b7b0;
  }
  * { margin: 0; padding: 0; box-sizing: border-box; }
  html, body {
    width: 1034px; height: 1200px; overflow: hidden;
    background: var(--backdrop);
    font-family: "Source Sans 3", "Helvetica Neue", Arial, sans-serif;
    color: var(--ink);
  }
  .canvas { position: relative; width: 1034px; height: 1200px; }

  .card {
    position: absolute; left: 64px; width: 882px; height: 507px;
    box-shadow: 0 6px 18px rgba(0,0,0,0.18);
    overflow: hidden;
  }
  .card--front { top: 51px; background: var(--card-white); }
  .card--back { top: 602px; background: var(--olive); }

  /* Front: brand block */
  .brand-block {
    position: absolute; left: 98px; top: 50px; width: 269px; height: 343px;
    display: flex; flex-direction: column; align-items: center; justify-content: center; gap: 28px;
  }
  .brand-block__square {
    width: 150px; height: 150px;
    background: linear-gradient(135deg, var(--olive) 0%, var(--olive-light) 100%);
  }
  .brand-block__name {
    font-weight: 600; font-size: 30px; line-height: 1.15; text-align: center;
    color: var(--ink);
  }

  .divider {
    position: absolute; left: 407px; top: 50px; width: 3px; height: 340px;
    background: linear-gradient(to bottom, rgba(185,183,176,0) 0%, var(--divider) 45%, var(--divider) 55%, rgba(185,183,176,0) 100%);
  }

  .contact { position: absolute; left: 448px; top: 50px; }
  .contact__name { font-weight: 700; font-size: 35px; line-height: 1; color: var(--ink-soft); }
  .contact__title { font-weight: 600; font-size: 21px; margin-top: 10px; color: var(--ink-soft); }
  .contact__company { font-weight: 400; font-size: 29px; line-height: 1.25; margin-top: 22px; color: var(--ink-soft); }
  .contact__address { font-size: 20px; line-height: 1.35; margin-top: 10px; color: var(--ink-soft); }
  .contact__lines { list-style: none; margin-top: 26px; }
  .contact__lines li {
    display: flex; align-items: center; gap: 10px;
    font-size: 25px; line-height: 1; margin-bottom: 16px; color: var(--ink);
  }
  .contact__lines svg { width: 18px; height: 18px; fill: var(--icon-grey); flex: none; }

  .footer-band { position: absolute; left: 0; bottom: 0; width: 882px; height: 80px; }
  .footer-band__url {
    position: absolute; right: 58px; bottom: 12px;
    font-size: 25px; letter-spacing: 2px; color: var(--ink);
  }

  /* Back */
  .back-brand {
    position: absolute; inset: 0;
    display: flex; align-items: center; justify-content: center; gap: 30px;
  }
  .back-brand__square { width: 90px; height: 90px; background: var(--card-white); }
  .back-brand__name {
    font-weight: 600; font-size: 52px; line-height: 1.1; color: var(--card-white);
  }
</style>
</head>
<body>
<div class="canvas">

  <section class="card card--front" aria-label="Business card front">
    <div class="brand-block">
      <div class="brand-block__square"></div>
      <div class="brand-block__name">Harlow Ridge<br>Building &amp; Construction</div>
    </div>

    <div class="divider"></div>

    <div class="contact">
      <p class="contact__name">Your Name</p>
      <p class="contact__title">Title</p>
      <p class="contact__company">Harlow Ridge Building<br>&amp; Construction</p>
      <p class="contact__address">00, Complex Name, Street<br>City 00000</p>
      <ul class="contact__lines">
        <li>
          <svg viewBox="0 0 24 24" aria-hidden="true"><path d="M6.6 10.8a15.1 15.1 0 0 0 6.6 6.6l2.2-2.2c.3-.3.7-.4 1-.2 1.1.4 2.3.6 3.6.6.6 0 1 .4 1 1V20c0 .6-.4 1-1 1A17 17 0 0 1 3 4c0-.6.4-1 1-1h3.5c.6 0 1 .4 1 1 0 1.3.2 2.5.6 3.6.1.3 0 .7-.2 1z"/></svg>
          (123) 456-7890
        </li>
        <li>
          <svg viewBox="0 0 24 24" aria-hidden="true"><path d="M8 1h8a2 2 0 0 1 2 2v18a2 2 0 0 1-2 2H8a2 2 0 0 1-2-2V3a2 2 0 0 1 2-2zm0 3v13h8V4zm4 15a1.2 1.2 0 1 0 0 2.4 1.2 1.2 0 0 0 0-2.4z"/></svg>
          (123) 456-7890
        </li>
        <li>
          <svg viewBox="0 0 24 24" aria-hidden="true"><path d="M2 5h20v14H2zm2 2v.5l8 5 8-5V7zm0 2.8V17h16V9.8l-8 5z"/></svg>
          yourname@harlowridge.com
        </li>
      </ul>
    </div>

    <svg class="footer-band" viewBox="0 0 882 80" preserveAspectRatio="none" aria-hidden="true">
      <path d="M0 46 L440 38 C470 37 480 33 494 22 C508 10 520 0 560 0 L882 0 L882 80 L0 80 Z" fill="var(--olive)"/>
      <path d="M0 42 L430 34 C462 33 474 28 490 16 C470 38 450 44 420 46 L0 54 Z" fill="var(--ink)"/>
    </svg>
    <span class="footer-band__url">www.harlowridge.com</span>
  </section>

  <section class="card card--back" aria-label="Business card back">
    <div class="back-brand">
      <div class="back-brand__square"></div>
      <div class="back-brand__name">Harlow Ridge<br>Building &amp; Construction</div>
    </div>
  </section>

</div>
</body>
</html>
```